Business Cards for new orthopaedic surgery practice

My husband and I are starting our own orthopaedic surgery practice. We are looking for a business card that is uniform, but one will have my name/title and the other will have his. You can just create one design with my name on it for now. But when I choose your design as the winning design I will ask that you add another copy with his name/title.

We are looking for classy, simple, elite all in one. We like dark blues/a little gold/yellow. Something that goes with our logo. We want our logo incorporated. Here is all the info you need:
Business name: RV Bone & Vitality Center
Location: 38517 North Willowmere Ave
Maple Harbor, FL 33990
Phone: 954-218-4063
Fax: 954-582-7341
Email: info@myrvbonecare.example

Names: Lydia Vance, M.D.
Board Certified Hand and Upper Extremity Surgeon

Ebo Dansu, M.D.
Board Certified Hip & Knee Replacement/General Orthopaedic Surgeon

Can decide what you want to put on the back. Maybe a slogan:
Steady Hands. Built Around You

I am just going to upload our logo. The only thing is if we select you as the winning design, the location, and phone numbers may change. We will need your help to update that once fully solidified.

Industry/Entity Type

Medical

Contact Information for Business Card

Colors
0054AA
0677BA
7BADD7
CADEEF
E8F1F8
0094D4
00A9DD
6FCCEA
C7EBF8
E9F6FB

Requirements
Must have
• class, appeal,
Should not have
• We want to air on the side of masculine if we are looking at masculine vs. feminine feel. But we still want it classy, sophisticated, and something we will love

```html
<!DOCTYPE html>
<html lang="en">
<head>
<meta charset="utf-8">
<title>RV Bone &amp; Vitality Center – Business Card</title>
<link rel="stylesheet" href="https://fonts.googleapis.com/css2?family=Montserrat:wght@400;500;600;700&display=swap">
<style>
  :root {
    --backdrop: #dedede;
    --card: #ffffff;
    --navy: #182a52;
    --ink: #111111;
    --gray: #555555;
    --gold: #b39a72;
  }
  * { margin: 0; padding: 0; box-sizing: border-box; }
  html, body { width: 1200px; height: 1200px; overflow: hidden; }
  body {
    background: var(--backdrop);
    font-family: "Montserrat", sans-serif;
    position: relative;
  }
  .card {
    position: absolute;
    left: 179px;
    width: 861px;
    height: 495px;
    background: var(--card);
    box-shadow: 0 10px 22px rgba(0, 0, 0, 0.18);
  }
  .card--front { top: 84px; }
  .card--back { top: 621px; }

  /* Front */
  .front-brand {
    position: absolute;
    left: 0; right: 0; top: 150px;
    text-align: center;
  }
  .front-brand__mark {
    display: inline-block;
    width: 64px; height: 64px;
    border-radius: 50%;
    background: var(--navy);
    margin-bottom: 20px;
  }
  .front-brand__name {
    font-size: 32px;
    font-weight: 600;
    color: var(--navy);
    letter-spacing: 0.5px;
  }
  .front-tagline {
    position: absolute;
    left: 0; right: 0; top: 420px;
    text-align: center;
    font-size: 28px;
    font-weight: 400;
    color: var(--gray);
    letter-spacing: 0.4px;
  }

  /* Back */
  .practice-name {
    position: absolute;
    left: 33px; top: 26px;
    font-size: 40px;
    font-weight: 600;
    color: var(--ink);
    letter-spacing: 0.8px;
  }
  .gold-rule {
    position: absolute;
    left: 32px; right: 34px; top: 89px;
    height: 6px;
    background: var(--gold);
  }
  .doctor-name {
    position: absolute;
    left: 32px; top: 109px;
    font-size: 32px;
    font-weight: 600;
    color: var(--navy);
  }
  .doctor-title {
    position: absolute;
    left: 32px; top: 154px;
    font-size: 23px;
    font-weight: 400;
    line-height: 32px;
    color: var(--gray);
    letter-spacing: 0.3px;
  }
  .contact-list {
    position: absolute;
    left: 32px; top: 324px;
    list-style: none;
  }
  .contact-list li {
    height: 38.5px;
    line-height: 34px;
    white-space: nowrap;
  }
  .contact-list .label {
    font-size: 26px;
    font-weight: 500;
    color: var(--navy);
    margin-right: 6px;
  }
  .contact-list .value {
    font-size: 22px;
    font-weight: 400;
    color: var(--gray);
    letter-spacing: 0.3px;
  }
  .back-brand {
    position: absolute;
    right: 34px; top: 330px;
    display: flex;
    align-items: center;
    gap: 10px;
  }
  .back-brand__mark {
    width: 34px; height: 34px;
    border-radius: 50%;
    background: var(--navy);
  }
  .back-brand__name {
    font-size: 21px;
    font-weight: 600;
    color: var(--navy);
  }
  .address {
    position: absolute;
    right: 34px; top: 410px;
    text-align: right;
    font-size: 21px;
    font-weight: 400;
    line-height: 31px;
    color: var(--gray);
    letter-spacing: 0.2px;
  }
</style>
</head>
<body>
  <section class="card card--front">
    <div class="front-brand">
      <span class="front-brand__mark"></span>
      <div class="front-brand__name">RV Bone &amp; Vitality Center</div>
    </div>
    <p class="front-tagline">Steady Hands. Built Around You</p>
  </section>

  <section class="card card--back">
    <h1 class="practice-name">RV Bone &amp; Vitality Center</h1>
    <div class="gold-rule"></div>
    <h2 class="doctor-name">Lydia Vance, M.D.</h2>
    <p class="doctor-title">Board Certified Hand and<br>Upper Extremity Surgeon</p>

    <ul class="contact-list">
      <li><span class="label">Phone.</span><span class="value">954-218-4063</span></li>
      <li><span class="label">Fax.</span><span class="value">954-582-7341</span></li>
      <li><span class="label">Email.</span><span class="value">info@myrvbonecare.example</span></li>
      <li><span class="label">Website.</span><span class="value">myrvbonecare.example</span></li>
    </ul>

    <div class="back-brand">
      <span class="back-brand__mark"></span>
      <span class="back-brand__name">RV Bone &amp; Vitality Center</span>
    </div>
    <p class="address">38517 North Willowmere Ave<br>Maple Harbor, FL 33990</p>
  </section>
</body>
</html>
```